Business Cards for new orthopaedic surgery practice

My husband and I are starting our own orthopaedic surgery practice. We are looking for a business card that is uniform, but one will have my name/title and the other will have his. You can just create one design with my name on it for now. But when I choose your design as the winning design I will ask that you add another copy with his name/title.

We are looking for classy, simple, elite all in one. We like dark blues/a little gold/yellow. Something that goes with our logo. We want our logo incorporated. Here is all the info you need:
Business name: RV Bone & Vitality Center
Location: 38517 North Willowmere Ave
Maple Hollow, FL 33418
Phone: 954-218-4063
Fax: 954-582-7341
Email: info@myrvbonecare.example

Names: Lydia Vance, M.D.
Board Certified Hand and Upper Extremity Surgeon

Ebo Dansu, M.D.
Board Certified Hip & Knee Replacement/General Orthopaedic Surgeon

Can decide what you want to put on the back. Maybe a slogan:
Grounded in Care. Centered on You

I am just going to upload our logo. The only thing is if we select you as the winning design, the location, and phone numbers may change. We will need your help to update that once fully solidified.

Industry/Entity Type

Medical

Contact Information for Business Card

Colors
0054AA
0677BA
7BADD7
CADEEF
E8F1F8
0094D4
00A9DD
6FCCEA
C7EBF8
E9F6FB

Requirements
Must have
• class, appeal,
Should not have
• We want to air on the side of masculine if we are looking at masculine vs. feminine feel. But we still want it classy, sophisticated, and something we will love

```html
<!DOCTYPE html>
<html lang="en">
<head>
<meta charset="utf-8">
<title>RV Bone &amp; Vitality Center — Business Card</title>
<link href="https://fonts.googleapis.com/css2?family=Montserrat:wght@800&family=Poppins:wght@400;500&family=Cinzel:wght@500&display=swap" rel="stylesheet">
<style>
  :root {
    --page: #eceff0;
    --gold-deep: #c29a56;
    --gold-warm: #b98d48;
    --gold-light: #dcc396;
    --navy: #1e3a94;
    --slate: #243040;
    --cream: #f5ead2;
  }
  * { margin: 0; padding: 0; box-sizing: border-box; }
  html, body { width: 1200px; height: 900px; overflow: hidden; background: var(--page); }
  .canvas {
    width: 1200px; height: 900px;
    display: flex; flex-direction: column; align-items: center; justify-content: center; gap: 40px;
  }
  .card {
    position: relative; width: 700px; height: 400px; overflow: hidden;
    box-shadow: 0 10px 28px rgba(40, 40, 40, .18);
  }
  .card__texture {
    position: absolute; inset: 0;
    background: radial-gradient(circle at 30% 45%, rgba(120, 90, 50, .16), transparent 45%),
                radial-gradient(circle at 75% 60%, rgba(120, 90, 50, .12), transparent 40%);
  }

  /* Front */
  .card--front { display: flex; }
  .front__contact { position: relative; width: 410px; background: linear-gradient(160deg, var(--gold-deep), var(--gold-warm)); }
  .front__brand { position: relative; flex: 1; background: var(--gold-light); display: flex; align-items: center; justify-content: center; }

  .identity { position: absolute; top: 54px; left: 0; display: flex; gap: 16px; align-items: stretch; }
  .identity__bar { width: 16px; background: var(--navy); }
  .identity__name {
    font-family: "Montserrat", sans-serif; font-weight: 800; font-size: 30px;
    color: var(--navy); letter-spacing: 1.5px; line-height: 1.05;
  }
  .identity__title {
    font-family: "Montserrat", sans-serif; font-weight: 800; font-size: 9.5px;
    color: var(--navy); letter-spacing: .6px; margin-top: 5px;
  }

  .contact-list { position: absolute; top: 150px; left: 0; list-style: none; display: flex; flex-direction: column; gap: 16px; }
  .contact-item { display: flex; align-items: center; gap: 16px; }
  .contact-item__tab {
    width: 68px; height: 30px; background: var(--navy);
    display: flex; align-items: center; justify-content: flex-end; padding-right: 4px;
    border-radius: 0 15px 15px 0;
  }
  .contact-item__icon {
    width: 24px; height: 24px; border-radius: 50%; background: var(--cream);
    display: flex; align-items: center; justify-content: center;
  }
  .contact-item__icon svg { width: 14px; height: 14px; }
  .contact-item__text { font-family: "Poppins", sans-serif; font-size: 17px; color: var(--navy); line-height: 1.25; }

  .wordmark { position: relative; display: flex; align-items: center; gap: 16px; }
  .wordmark__dot { width: 18px; height: 18px; border-radius: 50%; background: var(--navy); }
  .wordmark__rule { width: 3px; height: 96px; background: var(--navy); }
  .wordmark__text {
    font-family: "Cinzel", serif; font-weight: 500; font-size: 22px;
    color: var(--navy); line-height: 1.1; text-transform: uppercase;
  }

  /* Back */
  .card--back { background: linear-gradient(160deg, var(--gold-deep), var(--gold-warm)); display: flex; flex-direction: column; align-items: center; justify-content: center; gap: 14px; }
  .back__dot { position: relative; width: 26px; height: 26px; border-radius: 50%; background: var(--navy); }
  .back__name {
    position: relative; font-family: "Cinzel", serif; font-weight: 500; font-size: 40px;
    color: var(--navy); text-transform: uppercase; text-align: center; line-height: 1.1;
  }
  .back__sub { position: relative; display: flex; align-items: center; gap: 14px; font-family: "Cinzel", serif; font-weight: 500; font-size: 30px; color: var(--navy); }
  .back__sub::before, .back__sub::after { content: ""; width: 90px; height: 2px; background: var(--navy); }
  .slogan {
    position: relative; margin-top: 18px; background: var(--slate); color: var(--cream);
    font-family: "Poppins", sans-serif; font-size: 20px; letter-spacing: .5px;
    padding: 12px 36px; border-radius: 30px;
  }
</style>
</head>
<body>
<main class="canvas">
  <article class="card card--front">
    <section class="front__contact">
      <div class="card__texture" role="img" aria-label="Faint spine illustration over a dotted network pattern"></div>
      <header class="identity">
        <span class="identity__bar"></span>
        <div>
          <h1 class="identity__name">LYDIA VANCE, M.D.</h1>
          <p class="identity__title">BOARD CERTIFIED HAND AND UPPER EXTREMITY SURGEON</p>
        </div>
      </header>
      <ul class="contact-list">
        <li class="contact-item">
          <span class="contact-item__tab"><span class="contact-item__icon">
            <svg viewBox="0 0 24 24"><path fill="#1e3a94" d="M6.6 10.8a15 15 0 0 0 6.6 6.6l2.2-2.2c.3-.3.7-.4 1-.2 1.1.4 2.3.6 3.6.6.6 0 1 .4 1 1V20c0 .6-.4 1-1 1A17 17 0 0 1 3 4c0-.6.4-1 1-1h3.5c.6 0 1 .4 1 1 0 1.3.2 2.5.6 3.6.1.3 0 .7-.2 1z"/></svg>
          </span></span>
          <span class="contact-item__text">954-218-4063</span>
        </li>
        <li class="contact-item">
          <span class="contact-item__tab"><span class="contact-item__icon">
            <svg viewBox="0 0 24 24"><path fill="#1e3a94" d="M7 3h10v5H7zM4 9h16a2 2 0 0 1 2 2v6h-4v4H6v-4H2v-6a2 2 0 0 1 2-2zm4 7v3h8v-3z"/></svg>
          </span></span>
          <span class="contact-item__text">954-582-7341</span>
        </li>
        <li class="contact-item">
          <span class="contact-item__tab"><span class="contact-item__icon">
            <svg viewBox="0 0 24 24"><path fill="none" stroke="#1e3a94" stroke-width="2" d="M3 6h18v12H3zM3 6l9 7 9-7"/></svg>
          </span></span>
          <span class="contact-item__text">info@myrvbonecare.example</span>
        </li>
        <li class="contact-item">
          <span class="contact-item__tab"><span class="contact-item__icon">
            <svg viewBox="0 0 24 24"><path fill="#1e3a94" d="M12 2a7 7 0 0 0-7 7c0 5 7 13 7 13s7-8 7-13a7 7 0 0 0-7-7zm0 9.5A2.5 2.5 0 1 1 12 6.5a2.5 2.5 0 0 1 0 5z"/></svg>
          </span></span>
          <span class="contact-item__text">38517 North Willowmere Ave<br>Maple Hollow, FL 33418</span>
        </li>
      </ul>
    </section>
    <section class="front__brand">
      <div class="card__texture" role="img" aria-label="Faint spine illustration over a dotted network pattern"></div>
      <div class="wordmark">
        <span class="wordmark__dot"></span>
        <span class="wordmark__rule"></span>
        <p class="wordmark__text">RV Bone &amp;<br>Vitality<br>Center</p>
      </div>
    </section>
  </article>

  <article class="card card--back">
    <div class="card__texture" role="img" aria-label="Faint spine illustration over a dotted network pattern"></div>
    <span class="back__dot"></span>
    <h2 class="back__name">RV Bone &amp; Vitality</h2>
    <p class="back__sub">CENTER</p>
    <p class="slogan">Grounded in Care. Centered on You</p>
  </article>
</main>
</body>
</html>
```